Yoga/movement guide/teacher for adult yoga practice and kid yoga

What is the positioning or mission statement of your company? to guide individuals in a yoga-based safe and sustainable movement practice applicable to all ages and body types. Currently my focus is working with children in daycare and school settings, but my goal is to expand into private yoga practice for adults, and potentially as part of rented space in studios. I hope to find a way to work with children AND adults (so would love for logo to be appealing to both), but current focus is with children based on need and demand in the community. yoga for children also compliments my backround as a pediatrician/neonatologist, and I greatly miss interacting with children. I also want to emphasize a yoga/movement practice that is focused more on what one feels internally through movement. NOT what one looks like asthetically. I believe in removing all mirrors from yoga/movement practice. It should be an experience of movement/poses/yoga through appropriate cueing and education. It is not about the details of how far the knee should bend, or how high the leg should be. Focusing on foudation first, core, then core engagement and ultimately expression of poses/movements. A focus on strength, stability and mobility, not just flexibility, which is the common perception/association with yoga. I also want individuals to learn to be an advocate of their own health. Through guidance, I hope for individuals to connect with their body so they know themselves so well to be able to advocate for themselves in the modern healthcare world. This internal experience and connection is so essential in a world where modern medicine has become a business and it is all about making a dollar. the connection with patients is lost, and individuals need to learn to empower themselves and through their new found voice to be able to articulate what is wrong.<br/>Does your company have a tagline or slogan that should be included with the logo? "Practice Radiant Movement"<br/>What do you hope your company can be known for? Accessible yoga for a sustained practice. A guided movement practice where one gains information and knowledge of oneself through a mind/body connection. For one feel good physically with a new awaraness of their internal radiance that exists in all beings. Physical rejuvenation egnites a light and increases energy to flow through the physical body, which ultimately tranlates into works of kindness for others and out in the world. <br/>What color palettes might you prefer? why? love the colors currently chosen<br/>Where will the logo be primarily used? initially business cards, but hopefully future websites, t-shirts, and potentially local magazine adds. Also starting with a small couple of banners for community events in the area. I currently practice as a nomad out of my car :)<br/>Are there any elements you would prefer to see in the logo? Movement. A modern depiction of a human body/figure practicing movement. Hoping to avoid a stereotypical yoga pose per say, just because I want to people to think of it more of a movement practice with yoga roots. Modern yoga. There are elements of breathing and connecting with oneself through the flow of breath and movement, but I do not focus on the meditative/cerebral aspect of the yoga practice. What I teach is almost reaching a meditative state through movement. I personally don't practice, nor resonate with just seated meditation. just not my thing :)<br/>In your opinion, what defines a well-designed logo? curiosity. enough info for individuals to think they know what it means, but want to know more. invokes curiosity, but not too abstract. Reproducible. not too complicated. I want also to invoke a community feel, so a design that appeals to all people within a community. <br/>What is your preference in reference to icons, typography, spokespeople (characters), etc.? modern design. I love the idea of a logo for my purposes, to invoke a sense of movement from within. So not too static. <br/>What words or icons must be included in the logo? movement with yoga roots. <br/>What logos do you like and why? A representation, but not exact. I think some ambiguity is intriguing for others, and also memorable. I want it to be an artistic representation of movement/yoga<br/>What logos do you dislike and why? too busy, too loud. <br/>In your opinion, what is the primary purpose for a logo? association<br/>Who is the primary target audience? (who is most likely to use your services/product?) Children and their parents, but ultimately to expand into teaching adults. I even have aspirations of prenatal and post-natal yoga. Potentially incorporating infants. <br/>Who currently uses your product the most? n/a (working in schools/daycare currently. It is currently all volunteer)<br/>Are you pleased with the range of people your company serves? n/a<br/>Are you looking to expand, modify, or completely change your target audience? or will it remain the same? yes! expand into an adult audience. <br/>How do you plan to focus on your target audience? currently by working through schools and daycares. hopefully ultimately through after school care programs and then offering kid yoga in an existing yoga studio (working on this with Q Studio in Ridgeland, currently)<br/>What are your main forms of advertising? word of mouth, schools, daycares. Happy kids talking to their parents about the yoga class they took and happy teachers :)<br/>How do most customers find out about your company?<br/>Which gender are you targeting? All genders! However, with kid yoga, often the maternal individual in the child's life is more involved with decision making as far as extracurricular activities

Target Market(s)

individuals and families interested in wellness and feeling great

Contact Information for Business Card

Dana Whitford
Yoga Instructor
RYT-200, RCYT

certified yoga teacher for adults and children

Colors

Designer to choose colors to be used in the design.

Requirements
Must have
• "Practice Radiant Movement"
Nice to have
• logo with same colors

```html
<!DOCTYPE html>
<html lang="en">
<head>
<meta charset="UTF-8">
<title>Brightwell Studios – Business Cards</title>
<link rel="stylesheet" href="https://fonts.googleapis.com/css2?family=Roboto:wght@300;400;700&display=swap">
<style>
  :root {
    --backdrop: #3b3b3b;
    --card-grey: #7d7e7d;
    --aqua: #62c7cf;
    --sun: #f6dc3c;
    --white: #ffffff;
    --font: "Roboto", sans-serif;
  }
  * { box-sizing: border-box; margin: 0; padding: 0; }
  html, body { width: 1200px; height: 901px; overflow: hidden; }
  body { background: var(--backdrop); font-family: var(--font); position: relative; }

  .card {
    position: absolute;
    width: 560px;
    height: 320px;
    overflow: hidden;
    box-shadow: 0 10px 24px rgba(0,0,0,.45);
  }

  /* Back of card */
  .card--back { left: 40px; top: 90px; background: var(--card-grey); }
  .brand-lockup {
    position: absolute; inset: 0;
    display: flex; align-items: center; justify-content: center;
    gap: 14px;
  }
  .brand-mark { width: 46px; height: 46px; border-radius: 50%; background: var(--sun); flex: none; }
  .brand-name { font-weight: 300; font-size: 34px; color: var(--white); letter-spacing: .5px; white-space: nowrap; }

  /* Front of card */
  .card--front { left: 600px; top: 500px; background: var(--aqua); }
  .accent-panel {
    position: absolute; left: 0; top: 0;
    width: 300px; height: 320px;
  }
  .corner-brand {
    position: absolute; right: 22px; top: 20px;
    font-weight: 300; font-size: 15px; color: var(--white); white-space: nowrap;
  }
  .contact {
    position: absolute; left: 330px; top: 118px; color: var(--white);
  }
  .contact__name {
    font-weight: 700; font-size: 19px; color: var(--sun);
    text-transform: uppercase; letter-spacing: .3px; white-space: nowrap;
  }
  .contact__title { font-weight: 400; font-size: 13px; margin-top: 2px; }
  .contact__address { font-weight: 300; font-size: 12px; line-height: 1.35; margin-top: 12px; }
  .contact__list { list-style: none; margin-top: 10px; font-size: 12px; font-weight: 300; line-height: 1.6; }
  .contact__list li { display: flex; align-items: center; gap: 7px; white-space: nowrap; }
  .contact__icon { width: 11px; height: 11px; flex: none; }
</style>
</head>
<body>

<section class="card card--back" aria-label="Card back">
  <div class="brand-lockup">
    <span class="brand-mark"></span>
    <span class="brand-name">Brightwell Studios</span>
  </div>
</section>

<section class="card card--front" aria-label="Card front">
  <svg class="accent-panel" viewBox="0 0 300 320" aria-hidden="true">
    <path d="M0 0 H120 Q40 120 130 200 Q200 260 260 320 H0 Z" fill="var(--sun)"/>
  </svg>
  <div class="corner-brand">Brightwell Studios</div>

  <div class="contact">
    <p class="contact__name">Dana Whitford</p>
    <p class="contact__title">Manager</p>
    <p class="contact__address">Your address, city<br>state, ZIP 0000</p>
    <ul class="contact__list">
      <li>
        <svg class="contact__icon" viewBox="0 0 12 12" aria-hidden="true"><path d="M2 1 L4.5 1 L5.5 3.8 L4 4.8 Q5 7 7.2 8 L8.2 6.5 L11 7.5 L11 10 Q6 11.5 2.5 7.5 Q0.5 4.5 2 1Z" fill="var(--sun)"/></svg>
        555-014-2100
      </li>
      <li>
        <svg class="contact__icon" viewBox="0 0 12 12" aria-hidden="true"><rect x="0.5" y="2.5" width="11" height="7" fill="var(--sun)"/><path d="M0.5 2.5 L6 6.5 L11.5 2.5" fill="none" stroke="var(--aqua)" stroke-width="1"/></svg>
        hello@brightwellmail.com
      </li>
      <li>
        <svg class="contact__icon" viewBox="0 0 12 12" aria-hidden="true"><circle cx="6" cy="6" r="5.5" fill="var(--sun)"/><path d="M0.5 6 H11.5 M6 0.5 Q3 6 6 11.5 M6 0.5 Q9 6 6 11.5" fill="none" stroke="var(--aqua)" stroke-width="0.8"/></svg>
        www.brightwellstudios.com
      </li>
    </ul>
  </div>
</section>

</body>
</html>
```